Tarlow Plumbing & Heating Limited needs a service and maintenance contract document design

Tarlow Plumbing & Heating Limited are a well established family owned and operated company.

We currently offer installation, service and repair services for gas, plumbing, heating and electrical work. We wish to offer service and maintenance plans for plumbing, heating and electrical for our domestic clients in the UK. We would like the brochure to incorporate our company logo and colours, and reflect the reliable, quality, 5 star service we offer our clients.
I have attached a brochure that a friends company uses to give a good idea of the structure of the plans we wish to offer. We want to give our customers a choice in what packages best suit their needs. However, the pricing structure and certain elements/content of what we offer will be slightly different due to our geographical location.

We would like to have the basic structure of the brochure put in place and the
text content editable to our specific needs. Looking for advice on this but we do have Acrobat DC if we need to edit the text ourselves?

We use our logo with "TARLOW" in white over a grey backgound.

Our website is - www.tarlow.plumbing
Facebook and twitter handle is - @TarlowHeating

Target Market(s)

UK domestic plumbing, heating, natural gas, LPG and electrical market. Both private homeowners and landlords. Please see both the domestic and landlord document files attached for an idea on what we'd like.

Colors

Designer to choose colors to be used in the design.

Requirements
Must have
• Would like the finished design to incorporate the branding and colours we already use. Professional, Contemporary designs that will stand out above our competition.
• The content of the brochures MUST be very similar in structure to the files I’ve attached to the brief.
• We are having many designs submitted that are just copying our website content. This is not what we are asking for.
• I would like the icons etc to be redesigned so they are ours and not copied.
• Please also see the Landlords brochure attached to the brief. We would like this to be a separate document but to reflect the same design as the homeowner design you submit.
• The content of the documents will need to be re worded for our own use but I'm happy to change this once the design element is in place.
• A4 sized pages as per the example I've attached
• Must be able to attach the document to our website for clients to download.
Nice to have
• A4 sized pages as per the examples I've attached
Should not have
• Please DO NOT copy the content from our website to create our service plan brochures. This is not what we are after. As above, we need the brochures to be like the ones we've provided but made to fit our brand.
• Thank you

```html
<!DOCTYPE html>
<html lang="en">
<head>
<meta charset="utf-8">
<title>Tarlow Plumbing &amp; Heating – Service Plan Brochure</title>
<link href="https://fonts.googleapis.com/css2?family=Open+Sans:wght@400;600;700;800&family=Oswald:wght@500;600&family=Satisfy&display=swap" rel="stylesheet">
<style>
:root{
  --stage:#2e2e2e;
  --paper:#ffffff;
  --blue:#1d8fd8;
  --blue-dark:#136fb0;
  --blue-pale:#e6f3fb;
  --orange:#f7941d;
  --orange-deep:#ee6a1c;
  --orange-pale:#fde3c2;
  --grey:#6d6e71;
  --ink:#4a4a4a;
  --photo-warm:#d9c3a8;
  --photo-cool:#b9cfdc;
  --badge:#f4c21f;
}
*{box-sizing:border-box;margin:0;padding:0}
html,body{width:887px;height:1200px;overflow:hidden;background:var(--stage)}
body{font-family:"Open Sans",Arial,sans-serif;color:var(--ink);position:relative}
.page{position:absolute;width:410px;height:560px;background:var(--paper);overflow:hidden;box-shadow:0 4px 14px rgba(0,0,0,.5)}
.page--back{left:30px;top:30px}
.page--cover{left:447px;top:30px}
.page--welcome{left:30px;top:610px}
.page--details{left:447px;top:610px}
.art{position:absolute;left:0;top:0}
.brand{position:absolute;display:flex;align-items:center;gap:7px;font-weight:800;color:var(--grey);letter-spacing:1px}
.brand__dot{width:18px;height:18px;border-radius:50%;background:var(--orange)}
.brand__sub{display:block;font-size:6px;font-weight:600;letter-spacing:.5px;color:var(--grey)}

/* back page */
.contact{position:absolute;left:34px;top:300px;font-size:8px;line-height:1.55;color:var(--grey)}
.contact strong{display:block;font-size:8.5px;color:var(--ink);margin-bottom:3px}
.page--back .brand{left:150px;top:440px;font-size:26px}
.page--back .brand__dot{width:30px;height:30px}

/* cover */
.page--cover .brand{right:20px;top:22px;font-size:18px}
.cover__title{position:absolute;left:22px;top:210px;font-family:"Oswald",sans-serif;font-weight:600;font-size:33px;line-height:1.08;color:var(--blue)}
.care-panel{position:absolute;left:244px;top:200px;width:166px;height:270px;background:var(--blue);color:#fff;padding:14px 16px}
.care-panel__title{font-family:"Satisfy",cursive;font-size:38px;line-height:1}
.care-panel__lead{font-size:10px;font-weight:600;margin:4px 0 10px}
.care-list{list-style:none}
.care-list li{display:flex;align-items:center;gap:8px;font-size:12px;font-weight:700;margin-bottom:6px}
.care-list svg{flex:none}
.partner-badge{position:absolute;right:18px;bottom:22px;width:38px;height:38px;border-radius:6px;background:var(--badge)}

/* welcome */
.page--welcome .brand{left:20px;top:18px;font-size:17px}
.welcome__band{position:absolute;left:0;top:70px;width:100%;height:40px;background:var(--blue);color:#fff;font-size:19px;font-weight:700;padding:8px 20px}
.welcome__intro{position:absolute;left:20px;top:120px;width:370px;font-size:8px;line-height:1.5}
.welcome__intro p+p{margin-top:4px}
.welcome__body{position:absolute;left:0;top:200px;width:100%;height:360px;background:var(--orange)}
.col{position:absolute;top:14px;width:180px;font-size:8px;line-height:1.5}
.col h3{font-size:12px;line-height:1.2;margin-bottom:6px}
.col--left{left:16px;color:#fff}
.col--right{left:210px;width:186px;background:#fff;top:0;height:330px;padding:12px}
.col--right h3{color:var(--orange-deep)}
.tick-list{list-style:none;margin-top:6px}
.tick-list li{padding-left:12px;position:relative;margin-bottom:3px}
.tick-list li::before{content:"";position:absolute;left:0;top:4px;width:6px;height:3px;border-left:1.5px solid currentColor;border-bottom:1.5px solid currentColor;transform:rotate(-45deg)}
.tick-list--accent{color:var(--orange-deep)}
.tick-list--blue{color:var(--blue)}
.tick-list--accent span,.tick-list--blue span{color:var(--ink)}
.photo{display:block;border-radius:2px}
.col__note{margin-top:8px}
.welcome__foot{position:absolute;left:0;bottom:0;width:100%;height:30px;background:var(--orange-deep)}

/* details */
.details__top{position:absolute;left:18px;top:26px;width:220px;font-size:8px;line-height:1.5}
.details__box{position:absolute;left:250px;top:22px;width:145px;height:155px;background:var(--blue)}
.details__cols{position:absolute;left:18px;top:200px;width:376px;display:flex;gap:12px}
.details__cols .dcol{flex:1;font-size:7.5px;line-height:1.5}
.dcol h4{font-size:10px;color:var(--orange-deep);margin:0 0 4px}
.dcol p+h4{margin-top:8px}
.details__wave{top:auto;bottom:0;height:90px}
</style>
</head>
<body>

<!-- Back page -->
<section class="page page--back">
  <svg class="art" width="410" height="560" viewBox="0 0 410 560">
    <path d="M0 120 C80 180 170 230 260 280" stroke="var(--orange)" stroke-width="22" fill="none"/>
    <path d="M0 150 C80 205 170 250 250 300" stroke="var(--blue)" stroke-width="6" fill="none"/>
    <circle cx="300" cy="120" r="100" fill="var(--photo-cool)" role="img" aria-label="Photo of engineer fitting pipework"/>
    <circle cx="180" cy="60" r="48" fill="var(--photo-warm)" role="img" aria-label="Photo of a warm radiator"/>
    <circle cx="340" cy="255" r="40" fill="var(--photo-warm)" role="img" aria-label="Photo of boiler controls"/>
    <circle cx="300" cy="120" r="100" fill="none" stroke="#fff" stroke-width="5"/>
    <circle cx="180" cy="60" r="48" fill="none" stroke="#fff" stroke-width="4"/>
    <circle cx="340" cy="255" r="40" fill="none" stroke="#fff" stroke-width="4"/>
  </svg>
  <div class="contact">
    <strong>Tarlow Plumbing &amp; Heating Limited</strong>
    Unit 4, Meadow Park<br>Halden, HL4 7PQ<br>T: 01632 960 418<br>www.tarlow.plumbing<br>@TarlowHeating
  </div>
  <div class="brand"><span class="brand__dot"></span>TARLOW</div>
</section>

<!-- Cover -->
<section class="page page--cover">
  <svg class="art" width="410" height="560" viewBox="0 0 410 560">
    <circle cx="95" cy="95" r="80" fill="var(--photo-warm)" role="img" aria-label="Photo of a plumber at work"/>
    <circle cx="250" cy="120" r="66" fill="var(--photo-cool)" role="img" aria-label="Photo of a tap being fitted"/>
    <circle cx="95" cy="95" r="80" fill="none" stroke="#fff" stroke-width="5"/>
    <circle cx="250" cy="120" r="66" fill="none" stroke="#fff" stroke-width="5"/>
    <path d="M0 190 C120 175 250 185 410 165" stroke="var(--blue)" stroke-width="3" fill="none"/>
    <path d="M0 470 C90 500 160 540 200 560 L0 560 Z" fill="var(--orange)"/>
    <path d="M0 500 C70 520 120 545 150 560" stroke="var(--blue)" stroke-width="4" fill="none"/>
  </svg>
  <div class="brand"><span class="brand__dot"></span>TARLOW</div>
  <h1 class="cover__title">CARING<br>FOR YOUR<br>ESSENTIAL<br>HOME<br>SERVICES</h1>
  <div class="care-panel">
    <div class="care-panel__title">We Care</div>
    <p class="care-panel__lead">We can care for your:</p>
    <ul class="care-list">
      <li><svg width="13" height="13" viewBox="0 0 13 13"><rect x="1" y="1" width="11" height="11" rx="2" fill="none" stroke="#fff" stroke-width="1.5"/><path d="M3.5 6.5l2 2 4-4" stroke="#fff" stroke-width="1.5" fill="none"/></svg>Boiler</li>
      <li><svg width="13" height="13" viewBox="0 0 13 13"><rect x="1" y="1" width="11" height="11" rx="2" fill="none" stroke="#fff" stroke-width="1.5"/><path d="M3.5 6.5l2 2 4-4" stroke="#fff" stroke-width="1.5" fill="none"/></svg>Controls</li>
      <li><svg width="13" height="13" viewBox="0 0 13 13"><rect x="1" y="1" width="11" height="11" rx="2" fill="none" stroke="#fff" stroke-width="1.5"/><path d="M3.5 6.5l2 2 4-4" stroke="#fff" stroke-width="1.5" fill="none"/></svg>Central heating</li>
      <li><svg width="13" height="13" viewBox="0 0 13 13"><rect x="1" y="1" width="11" height="11" rx="2" fill="none" stroke="#fff" stroke-width="1.5"/><path d="M3.5 6.5l2 2 4-4" stroke="#fff" stroke-width="1.5" fill="none"/></svg>Plumbing</li>
      <li><svg width="13" height="13" viewBox="0 0 13 13"><rect x="1" y="1" width="11" height="11" rx="2" fill="none" stroke="#fff" stroke-width="1.5"/><path d="M3.5 6.5l2 2 4-4" stroke="#fff" stroke-width="1.5" fill="none"/></svg>Drains</li>
      <li><svg width="13" height="13" viewBox="0 0 13 13"><rect x="1" y="1" width="11" height="11" rx="2" fill="none" stroke="#fff" stroke-width="1.5"/><path d="M3.5 6.5l2 2 4-4" stroke="#fff" stroke-width="1.5" fill="none"/></svg>Gas pipes</li>
      <li><svg width="13" height="13" viewBox="0 0 13 13"><rect x="1" y="1" width="11" height="11" rx="2" fill="none" stroke="#fff" stroke-width="1.5"/><path d="M3.5 6.5l2 2 4-4" stroke="#fff" stroke-width="1.5" fill="none"/></svg>Electrics</li>
      <li><svg width="13" height="13" viewBox="0 0 13 13"><rect x="1" y="1" width="11" height="11" rx="2" fill="none" stroke="#fff" stroke-width="1.5"/><path d="M3.5 6.5l2 2 4-4" stroke="#fff" stroke-width="1.5" fill="none"/></svg>Gas fires</li>
    </ul>
  </div>
  <div class="partner-badge"></div>
</section>

<!-- Welcome page -->
<section class="page page--welcome">
  <div class="brand"><span class="brand__dot"></span><span>TARLOW<span class="brand__sub">PLUMBING &amp; HEATING</span></span></div>
  <h2 class="welcome__band">Welcome to Warm &amp; Well</h2>
  <div class="welcome__intro">
    <p>Warm &amp; Well offers a simple way to keep your home running smoothly all year. Our engineers service your boiler, heating and plumbing, and we are on hand when things go wrong.</p>
    <p>Choose the plan that suits you, from a yearly boiler check to full cover for your home.</p>
  </div>
  <div class="welcome__body">
    <div class="col col--left">
      <h3>Caring for your home – and much more</h3>
      <p>Every plan includes a yearly service and priority repairs.</p>
      <ul class="tick-list">
        <li>Annual boiler service</li>
        <li>Heating system checks</li>
        <li>Priority call-outs</li>
        <li>Parts and labour</li>
        <li>Gas safety record</li>
        <li>Plumbing repairs</li>
        <li>24/7 helpline</li>
      </ul>
    </div>
    <div class="col col--right">
      <h3>Why choose a Warm &amp; Well package?</h3>
      <svg class="photo" width="162" height="120" viewBox="0 0 162 120" role="img" aria-label="Photo of a smiling homeowner by a radiator">
        <defs><linearGradient id="homeownerTone" x1="0" y1="0" x2="1" y2="1"><stop offset="0" stop-color="#e8d6c3"/><stop offset="1" stop-color="#c9b29a"/></linearGradient></defs>
        <rect width="162" height="120" fill="url(#homeownerTone)"/>
      </svg>
      <p class="col__note">Peace of mind from a local, family-run team you can trust.</p>
      <ul class="tick-list tick-list--accent">
        <li><span>Registered engineers</span></li>
        <li><span>No hidden charges</span></li>
        <li><span>Fast local response</span></li>
      </ul>
    </div>
  </div>
  <div class="welcome__foot"></div>
</section>

<!-- Details page -->
<section class="page page--details">
  <div class="details__top">
    <p>Your plan starts from the date of your first service.</p>
    <ul class="tick-list tick-list--blue">
      <li><span>Cover for one property</span></li>
      <li><span>Monthly or yearly payments</span></li>
      <li><span>Cancel within 14 days</span></li>
    </ul>
  </div>
  <div class="details__box"></div>
  <div class="details__cols">
    <div class="dcol">
      <h4>Your Warm &amp; Well plan</h4>
      <p>Pick the level of cover that works for your home and budget. We will book your first visit within two weeks.</p>
      <h4>The small print</h4>
      <p>Plans renew each year unless you tell us otherwise.</p>
    </div>
    <div class="dcol">
      <h4>Everything is covered</h4>
      <p>Boilers, controls, radiators, pipes and taps are all included, with no call-out fee on any visit.</p>
    </div>
    <div class="dcol">
      <h4>Keeping warm this winter</h4>
      <p>Bleed radiators, check your pressure and keep vents clear for a safe, efficient home.</p>
      <h4>What to do in a breakdown</h4>
      <p>Call our helpline and an engineer will be with you fast.</p>
    </div>
  </div>
  <svg class="art details__wave" width="410" height="90" viewBox="0 0 410 560" preserveAspectRatio="none">
    <path d="M0 520 C140 490 260 500 410 470 L410 560 L0 560 Z" fill="var(--orange)"/>
    <path d="M0 540 C140 515 260 525 410 500" stroke="var(--blue)" stroke-width="4" fill="none"/>
  </svg>
</section>

</body>
</html>
```